Whale Watching Voucher(ticket) Layout

Tidecrest.com.au would like a new design for their existing vouchers (tickets) being issued when a customer completes a purchase.
These vouchers are to be issued from within Salesforce CRM using Conga Composer (don't worry about that, we'll handle that) but that does mean that the voucher template needs to be designed and provided in Microsoft Word. The voucher will be sent via an email and we require a HTML email design also.
The following fields need to be included on the email/Voucher:
BOOKING CONFIRMATION NUMBER (e&v)
First Name (e&v)
Tour Name (e&v)
Tour Operator Name (e&v)
Telephone Contact (e&v)
Departure Date (e&v)
Party Name (e&v)
Adults Tickets (v)
Concession Tickets (v)
Child Tickets (v)
Infant Tickets (v)
Pickup Location (v)
Pickup Time (v)
Boarding Place (v)
Boarding Time (v)
Departure Time (v)
Return Time (v)
Terms and conditions (e&v) - this is quite a long description
What to Bring (v) - this is quite a long description
What to do if the Pick-up is more than 10 mins late (v) - this is a long description
What to do if you're late (v) - this is quite a long description
Booking Terms and Conditions
{!Opportunity.Tour_Terms_and_Conditions_PG1__c}
FREECALL 1800 463 927 (Australia)
International +61 7 3962 4718
Voxlink coastwander
(e&v indicate fields to be included on the Email and the Voucher)
(v indicate fields to be included on the Voucher only)
Updates
Project Deadline Extended
Reason: I realised the original Deadline didn't take weekends into account so have extended it to the end of this week. The Whale season is well underway so need to have it completed by Friday. Thanks all for your efforts.
I uploaded the current (text based) samples of the email & voucher that we are hoping you are going to be able to redesign for us.
Sorry for lack of feedback, I got caught up on another project. We are reviewing the designs tomorrow and will get back to you all.
Target Market(s)
Mid market Australian and International Tourists
Industry/Entity Type
Purchase
Requirements
Must have
- Consistency with existing Tidecrest.com.au & kelpmoor.com.au branding.
The Voucher should be designed to be printed out on a single A4 sheet.
Nice to have
- It would be good to have a paragraph/section referencing the kelpmoor.com.au logo and website on the email (not the voucher).
Any recommendation for additional information/fields that should/could be included not listed above will be gratefully received.
Happy for you to reword the labels to make them more friendly.

```html
<!DOCTYPE html>
<html lang="en">
<head>
<meta charset="utf-8">
<title>Tidecrest Tour Voucher</title>
<link rel="stylesheet" href="https://fonts.googleapis.com/css2?family=Didact+Gothic&family=Open+Sans:wght@600;700&display=swap">
<style>
  :root{
    --teal:#1a9e9c;
    --teal-text:#2a93a0;
    --green:#5aa65c;
    --green-text:#2d9a3e;
    --ink:#3a3a3a;
    --rule:#d8dcdc;
    --page:#f3f4f4;
    --white:#ffffff;
    --tag:#f08a1c;
  }
  *{box-sizing:border-box;margin:0;padding:0}
  html,body{width:1200px;height:834px;overflow:hidden}
  body{background:radial-gradient(ellipse at center,#fbfbfb 0%,var(--page) 70%,#e9eaea 100%);font-family:"Didact Gothic",sans-serif;color:var(--ink)}
  .stage{position:absolute;left:0;top:0;width:1254px;height:872px;transform:scale(.9569,.9564);transform-origin:0 0}
  .tag{position:absolute;left:0;top:28px;height:22px;width:98px;background:var(--tag);color:var(--white);font:700 14px "Open Sans",sans-serif;line-height:22px;padding-left:20px;clip-path:polygon(0 0,88% 0,100% 50%,88% 100%,0 100%)}
  .voucher{position:absolute;left:90px;top:58px;width:1077px;height:762px;background:linear-gradient(90deg,var(--teal) 0 50%,var(--green) 50% 100%);box-shadow:0 2px 6px rgba(0,0,0,.12)}
  .header{position:absolute;left:0;top:10px;width:100%;height:82px;background:var(--white)}
  .sites{position:absolute;left:27px;top:23px;font:700 16px "Open Sans",sans-serif;color:var(--teal-text);line-height:18px}
  .brand{position:absolute;top:28px;display:flex;align-items:center;gap:8px;font:700 17px "Open Sans",sans-serif;color:#5a9aa0}
  .brand .dot{width:36px;height:36px;border-radius:50%;background:var(--teal)}
  .brand.tidecrest{left:300px}
  .brand.kelpmoor{left:500px;color:#6a9a6a}
  .brand.kelpmoor .dot{background:var(--green)}
  .contact{position:absolute;right:18px;top:19px;text-align:right;font:700 15px "Open Sans",sans-serif;color:var(--green-text);line-height:19px}
  .panel{position:absolute;left:10px;top:102px;width:1057px;height:650px;background:var(--white)}
  .booking{position:absolute;left:2px;top:0;width:500px;height:42px;border-right:5px solid var(--teal);border-bottom:4px solid var(--teal);display:flex;align-items:center;padding-left:26px;font:600 15px "Open Sans",sans-serif;color:var(--teal-text)}
  .booking strong{font-size:19px;margin-left:36px;position:relative;top:-3px}
  .fields{position:absolute;left:18px;list-style:none;font-size:15.4px;line-height:18.4px;letter-spacing:.3px}
  .fields li{display:flex}
  .fields li::before{content:"";width:4px;height:4px;border-radius:50%;background:var(--teal);margin:8px 6px 0 0;flex:none}
  .fields .label{width:172px}
  .fields .colon{width:23px}
  .fields.tour{top:49px}
  .fields.pickup{top:250px}
  .divider{position:absolute;left:528px;top:25px;width:1px;height:325px;background:var(--rule)}
  .info{position:absolute;left:545px;top:27px;width:500px;list-style:none;font-size:15.4px;line-height:18.4px;letter-spacing:.3px}
  .info > li{position:relative;padding-left:9px;margin-bottom:18px}
  .info > li::before{content:"";position:absolute;left:0;top:8px;width:4px;height:4px;border-radius:50%;background:var(--teal)}
  .info .sub{padding-left:18px;text-indent:-10px}
  .blurb{position:absolute;left:33px;top:388px;width:991px;font-size:15.2px;line-height:18.3px;letter-spacing:.4px;text-align:justify}
  .prices{position:absolute;left:44px;top:500px;width:968px;border-collapse:collapse;font-size:15.4px;letter-spacing:.3px;box-shadow:0 1px 4px rgba(0,0,0,.15)}
  .prices th,.prices td{border:2px solid var(--teal);height:27px;font-weight:400}
  .prices th{color:var(--teal-text)}
  .prices .c1{width:355px}.prices .c2{width:131px}.prices .c3{width:248px}
</style>
</head>
<body>
<div class="stage">
  <div class="tag">voucher</div>
  <div class="voucher">
    <header class="header">
      <div class="sites">www.kelpmoor.com.au<br>tidecrest.com.au</div>
      <div class="brand tidecrest"><span class="dot"></span>Tidecrest</div>
      <div class="brand kelpmoor"><span class="dot"></span>Kelpmoor</div>
      <div class="contact">FREECALL 1800 463 927 (Australia)<br>International +61 7 3962 4718<br>Voxlink coastwander</div>
    </header>
    <section class="panel">
      <div class="booking">BOOKING CONFIRMATION NUMBER :<strong>-Af7862</strong></div>
      <ul class="fields tour">
        <li><span class="label">First Name</span><span class="colon">:</span>Marlo</li>
        <li><span class="label">Tour Name</span><span class="colon">:</span>1 Day Sandway Experience Trekker</li>
        <li><span class="label">Tour Operator Name</span><span class="colon">:</span>Sandway Experience Tours</li>
        <li><span class="label">Telephone Contact</span><span class="colon">:</span>1800 571 206</li>
        <li><span class="label">Departure Date</span><span class="colon">:</span>July 8th 2012</li>
        <li><span class="label">Party Name</span><span class="colon">:</span>Owen and Clare Hartley</li>
        <li><span class="label">Adults Tickets</span><span class="colon">:</span>4</li>
        <li><span class="label">Concession Tickets</span><span class="colon">:</span>2</li>
        <li><span class="label">Child Tickets</span><span class="colon">:</span>2</li>
        <li><span class="label">Infant Tickets</span><span class="colon">:</span>1</li>
      </ul>
      <ul class="fields pickup">
        <li><span class="label">Pickup Location</span><span class="colon">:</span>Bay Bed and Breakfast</li>
        <li><span class="label">Pickup Time</span><span class="colon">:</span>8am</li>
        <li><span class="label">Boarding Place</span><span class="colon">:</span>9am</li>
        <li><span class="label">Boarding Time</span><span class="colon">:</span>915am</li>
        <li><span class="label">Departure Time</span><span class="colon">:</span>930am</li>
        <li><span class="label">Return Time</span><span class="colon">:</span>6:00pm</li>
      </ul>
      <div class="divider"></div>
      <ul class="info">
        <li>Terms and condition<br>Tidecrest are agent for Norvale
          <div class="sub">- Please reconfirm your reservation and notify us of your pick up location 48 hours prior to departure.</div>
          <div class="sub">- Concessions Fare is only applicable to Seniors, Students, HSA and VIP card holders.</div></li>
        <li>What to Bring<br>Hat, sunscreen, sunglasses, camera, flat shoes and a smile!</li>
        <li>What to do if the Pick-up is more than 10 mins late<br>Waiting in the station</li>
        <li>What to do if you're late<br>Phone the operator</li>
        <li>Booking Terms and Conditions<br>July 9th 2012</li>
      </ul>
      <p class="blurb">Lorem Ipsum is simply dummy text of the printing and typesetting industry. Lorem Ipsum has been the industry's standard dummy text ever since the 1500s, when an unknown printer took a galley of type and scrambled it to make a type specimen book. It has survived not only five centuries, but also the leap into electronic typesetting, remaining essentially unchanged. It was popularised in the 1960s with the release of Typeway sheets containing Lorem Ipsum passages, and more recently with desktop publishing software like Layoutsmith including versions of Lorem Ipsum.</p>
      <table class="prices">
        <thead><tr><th class="c1">Ticket guest type</th><th class="c2">Qty</th><th class="c3">Sales price</th><th>Total price</th></tr></thead>
        <tbody>
          <tr><td></td><td></td><td></td><td></td></tr>
          <tr><td></td><td></td><td></td><td></td></tr>
          <tr><td></td><td></td><td></td><td></td></tr>
          <tr><td></td><td></td><td></td><td></td></tr>
        </tbody>
      </table>
    </section>
  </div>
</div>
</body>
</html>
```